Australian IT Company requires Business Card Design

Bluefinch is an Australian company that specialises in IT consulting & support, software development, project management, network services.

We have been in business for 15 years.

* We require a business card with the following on it:
Logo
Address
Contact Details
Space for staff name, title & mobile number

Industry/Entity Type

Software

```html
<!DOCTYPE html>
<html lang="en">
<head>
<meta charset="utf-8">
<title>Bluefinch Business Card</title>
<link rel="stylesheet" href="https://fonts.googleapis.com/css2?family=Open+Sans:wght@400;600&display=swap">
<style>
  :root {
    --page-bg: #e6e6e6;
    --brand-blue: #3d6f98;
    --panel-blue: #356185;
    --panel-grey: #6b7078;
    --card-white: #ffffff;
    --text-white: #ffffff;
    --icon-blue: #3d6f98;
  }
  * { box-sizing: border-box; margin: 0; padding: 0; }
  html, body { width: 1200px; height: 680px; overflow: hidden; }
  body {
    background: var(--page-bg);
    font-family: "Open Sans", Arial, sans-serif;
    position: relative;
  }
  .card {
    position: absolute;
    top: 185px;
    width: 540px;
    height: 310px;
    overflow: hidden;
    box-shadow: 0 6px 18px rgba(0,0,0,0.18);
  }
  .card--front { left: 40px; background: var(--brand-blue); color: var(--text-white); }
  .card--back { left: 620px; background: var(--card-white); }

  /* Front */
  .brand {
    position: absolute;
    left: 0; right: 0;
    top: 100px;
    display: flex;
    justify-content: center;
    align-items: center;
    gap: 14px;
  }
  .brand__dot {
    width: 30px; height: 30px;
    border-radius: 50%;
    background: var(--text-white);
  }
  .brand__name {
    font-weight: 600;
    font-size: 36px;
    line-height: 1;
    color: var(--text-white);
  }
  .brand__tagline {
    position: absolute;
    left: 0; right: 0;
    top: 152px;
    text-align: center;
    font-size: 11px;
    letter-spacing: 3px;
    text-transform: uppercase;
  }
  .front__web {
    position: absolute;
    left: 0; right: 0;
    bottom: 46px;
    text-align: center;
    font-size: 14px;
    letter-spacing: 4px;
  }

  /* Back */
  .info-band {
    position: absolute;
    left: 232px; right: 0;
    top: 46px; height: 180px;
    background: var(--panel-grey);
    color: var(--text-white);
  }
  .info-band__divider {
    position: absolute;
    left: 24px; top: 86px;
    width: 2px; height: 44px;
    background: var(--text-white);
  }
  .address {
    position: absolute;
    left: 50px; top: 16px;
    font-size: 13px;
    line-height: 16px;
  }
  .contact-list {
    position: absolute;
    left: 46px; top: 80px;
    list-style: none;
    font-size: 13px;
    line-height: 18px;
  }
  .contact-list li { display: flex; align-items: center; gap: 8px; }
  .contact-list svg { width: 11px; height: 11px; flex: none; }
  .name-panel {
    position: absolute;
    left: 30px; top: 108px;
    width: 196px; height: 162px;
    background: var(--panel-blue);
    color: var(--text-white);
  }
  .staff-name {
    position: absolute;
    left: 22px; top: 86px;
    font-size: 19px;
  }
  .staff-title {
    position: absolute;
    left: 30px; top: 113px;
    font-size: 13px;
  }
</style>
</head>
<body>
  <section class="card card--front" aria-label="Card front">
    <div class="brand">
      <span class="brand__dot"></span>
      <span class="brand__name">Bluefinch</span>
    </div>
    <p class="brand__tagline">Technology you can trust</p>
    <p class="front__web">www.bluefinch.net.au</p>
  </section>

  <section class="card card--back" aria-label="Card back">
    <div class="info-band">
      <span class="info-band__divider"></span>
      <p class="address">14 Harbour Lane<br>Unit Block 3<br>Kewdale WA 6105</p>
      <ul class="contact-list">
        <li>
          <svg viewBox="0 0 12 12" aria-hidden="true"><circle cx="6" cy="6" r="5.5" fill="none" stroke="var(--icon-blue)" stroke-width="1.2"/><path d="M4 3.5 L5 3.5 L5.5 5 L4.8 5.6 Q5.5 7 6.6 7.3 L7.2 6.6 L8.6 7.2 L8.6 8.3 Q5.5 8.7 4 3.5Z" fill="var(--icon-blue)"/></svg>
          +61 3 5550 4110
        </li>
        <li>
          <svg viewBox="0 0 12 12" aria-hidden="true"><rect x="3" y="1" width="6" height="10" rx="1" fill="none" stroke="var(--icon-blue)" stroke-width="1.2"/><rect x="5" y="9" width="2" height="1" fill="var(--icon-blue)"/></svg>
          +61 3 5550 4000
        </li>
        <li>
          <svg viewBox="0 0 12 12" aria-hidden="true"><rect x="1" y="2.5" width="10" height="7" fill="var(--icon-blue)"/><path d="M1 2.5 L6 6.5 L11 2.5" fill="none" stroke="var(--panel-grey)" stroke-width="1"/></svg>
          liam@bluefinch.net.au
        </li>
        <li>
          <svg viewBox="0 0 12 12" aria-hidden="true"><circle cx="6" cy="6" r="5" fill="none" stroke="var(--icon-blue)" stroke-width="1.2"/><ellipse cx="6" cy="6" rx="2.2" ry="5" fill="none" stroke="var(--icon-blue)" stroke-width="1"/><path d="M1 6 H11" stroke="var(--icon-blue)" stroke-width="1"/></svg>
          www.bluefinch.net.au
        </li>
      </ul>
    </div>
    <div class="name-panel">
      <p class="staff-name">Liam Hartley</p>
      <p class="staff-title">Manager</p>
    </div>
  </section>
</body>
</html>
```